New Business Card (to reflect updated website content and graphics)

I changed some text and graphics on my website, so I need a new business card.

Target Market(s)

Mostly women, ages 30 - 60.

Industry/Entity Type

Life Coaching

Contact Information for Business Card

Included in attached Word document

Font styles to use
Sans Serif

Requirements
Must have
• I am not a creative person, so I will defer to designer. Take a look at my website, and you can get a feel for me, my style, and my target audience. Thank You!

My 3 branding colors are included in attached Word document.

```html
<!DOCTYPE html>
<html lang="en">
<head>
<meta charset="utf-8">
<title>Bright Harbor Coaching – Business Card</title>
<link href="https://fonts.googleapis.com/css2?family=Montserrat:wght@400;500&display=swap" rel="stylesheet">
<style>
  :root {
    --teal: #2a97b1;
    --coral: #ef7363;
    --ink: #2c3540;
    --paper: #ffffff;
    --backdrop: #ebecee;
    --rule: #3a4450;
    --cloud-light: #dceff4;
    --cloud-warm: #f3c2ba;
  }
  * { margin: 0; padding: 0; box-sizing: border-box; }
  html, body { width: 1200px; height: 900px; overflow: hidden; }
  body {
    background: var(--backdrop);
    font-family: "Montserrat", sans-serif;
    position: relative;
  }
  .card {
    position: absolute;
    left: 300px;
    width: 600px;
    height: 343px;
    border-radius: 22px;
    box-shadow: 0 6px 18px rgba(0,0,0,0.18);
    overflow: hidden;
  }
  .card--front { top: 60px; background: var(--teal); }
  .card--back { top: 470px; background: var(--paper); }

  .front__artwork {
    position: absolute;
    left: 180px; top: 50px;
    width: 240px; height: 210px;
    border-radius: 12px;
    background: linear-gradient(135deg, var(--cloud-light) 0%, var(--cloud-warm) 50%, var(--cloud-light) 100%);
    opacity: 0.85;
  }
  .front__brand {
    position: absolute;
    right: 30px; bottom: 30px;
    color: var(--paper);
    font-size: 13px;
    font-weight: 400;
    letter-spacing: 0.12em;
    text-transform: uppercase;
  }

  .back__brand {
    position: absolute;
    left: 40px; top: 44px;
    color: var(--teal);
    font-size: 22px;
    font-weight: 500;
    letter-spacing: 0.04em;
  }
  .back__rule {
    position: absolute;
    left: 40px;
    width: 360px;
    height: 1px;
    background: var(--rule);
  }
  .back__rule--top { top: 96px; }
  .back__rule--bottom { top: 226px; }
  .back__name {
    position: absolute;
    left: 40px; top: 112px;
    color: var(--teal);
    font-size: 24px;
    font-weight: 500;
  }
  .back__titles {
    position: absolute;
    left: 40px; top: 148px;
    list-style: none;
    color: var(--ink);
    font-size: 13px;
    line-height: 1.5;
  }
  .back__contacts {
    position: absolute;
    left: 40px; top: 238px;
    list-style: none;
    color: var(--ink);
    font-size: 13px;
    line-height: 1;
  }
  .contact { display: flex; align-items: center; gap: 10px; margin-bottom: 9px; }
  .contact__icon { width: 14px; height: 14px; flex: none; }
</style>
</head>
<body>

<section class="card card--front" aria-label="Card front">
  <div class="front__artwork" role="img" aria-label="Heart-shaped word cloud of coaching themes such as hope, joy, love, peace and clarity, with the phrase feel better, live well"></div>
  <div class="front__brand">Bright Harbor Coaching</div>
</section>

<section class="card card--back" aria-label="Card back">
  <div class="back__brand">Bright Harbor Coaching</div>
  <div class="back__rule back__rule--top"></div>
  <h1 class="back__name">Marla Denning</h1>
  <ul class="back__titles">
    <li>Certified Professional Life Coach</li>
    <li>Health &amp; Wellness Coach</li>
    <li>Advanced Grief Healing Pathway Specialist</li>
  </ul>
  <div class="back__rule back__rule--bottom"></div>
  <ul class="back__contacts">
    <li class="contact">
      <svg class="contact__icon" viewBox="0 0 16 16" aria-hidden="true"><path d="M3 1h3l1.5 4-2 1.3a9 9 0 0 0 4.2 4.2L11 8.5l4 1.5v3a2 2 0 0 1-2 2A12 12 0 0 1 1 3a2 2 0 0 1 2-2z" fill="var(--teal)"/></svg>
      <span>(555) 014-2277</span>
    </li>
    <li class="contact">
      <svg class="contact__icon" viewBox="0 0 16 16" aria-hidden="true"><rect x="1.5" y="3.5" width="13" height="9" fill="none" stroke="var(--teal)" stroke-width="1.5"/><path d="M1.5 3.5 8 9l6.5-5.5" fill="none" stroke="var(--teal)" stroke-width="1.5"/></svg>
      <span>marla@brightharborcoaching.com</span>
    </li>
    <li class="contact">
      <svg class="contact__icon" viewBox="0 0 16 16" aria-hidden="true"><circle cx="8" cy="8" r="6.5" fill="none" stroke="var(--teal)" stroke-width="1.5"/><path d="M1.5 8h13M8 1.5c-3 3.5-3 9.5 0 13M8 1.5c3 3.5 3 9.5 0 13" fill="none" stroke="var(--teal)" stroke-width="1.2"/></svg>
      <span>brightharborcoaching.com</span>
    </li>
  </ul>
</section>

</body>
</html>
```